Medical consulting firm needs polished website

I am a physician and working on setting up a smal consulting firm in New Hampshire, USA. It is called Bright Harbor Medical Services, LLC and the website will be BrightHarborMed.com. I was puttering around at making my own website, and it just didn't come together nicely so I've decided to leave it to the pros. The focus of the business is Advanced Care Planning, ie planning for your future medical needs. So it deals with some heavy stuff like planning for if you get sick, who should make decisions for you, end of life options etc. So it can't be too flippant or cutesy, but also can't be too dour and dark. I am hoping to convey that by thinking ahead and making some plans you can lift some of the worries off of yourself and your family - and that we can help make a scary sounding path more manageable. I want it to be made with wordpress and I have actually already bought a template ( Vitarun – A Modern Multidisciplinary Medical & Health Theme ). The website needs to have general information about our services, doc profile, appointment maker, blog/url link page, and ideally web commerce application ( the template has access to woocommerce). I've posted my business card and current brochure (still tweaking them, but you get the idea). I am also partnering with lumenfold.com and so have included their logo and would want connections/info about them. I have the logos etc in different formats as needed.

Target Market(s)

middle aged to older adults

Industry/Entity Type

Medical

Coding

Coded - Design and coding required

Font styles to use
Sans Serif

Requirements
Must have
• as above.
Nice to have
• Ease of reading/access for elderly viewers. woo commerce.

```html
<!DOCTYPE html>
<html lang="en">
<head>
<meta charset="utf-8">
<title>Bright Harbor Medical Services</title>
<link href="https://fonts.googleapis.com/css2?family=Open+Sans:wght@400;600;700&display=swap" rel="stylesheet">
<style>
:root{
  --blue:#2f8fef;
  --blue-dark:#1f78d6;
  --green:#38c21f;
  --ink:#2b2b2b;
  --muted:#6d6d6d;
  --light:#f2f2f2;
  --grey:#e4e4e4;
  --white:#fff;
}
*{box-sizing:border-box;margin:0;padding:0}
html,body{width:1200px;height:3435px;overflow:hidden}
body{font-family:"Open Sans",Arial,sans-serif;color:var(--ink);background:var(--white);position:relative}
.wrap{width:1008px;margin:0 auto;position:relative}
/* header */
.topbar{height:126px;display:flex;align-items:center}
.topbar .wrap{display:flex;align-items:center}
.brand{display:flex;align-items:center;gap:14px;width:452px}
.brand-dot{width:70px;height:70px;border-radius:50%;background:var(--blue)}
.brand-name{font-size:34px;font-weight:600;color:var(--blue)}
.info{display:flex;align-items:center;gap:14px;font-size:15px;color:var(--muted);line-height:1.6}
.info svg{flex:none}
.info strong{color:var(--ink);font-weight:600}
.info.hours{margin-left:70px}
.socials{margin-left:auto;display:flex;gap:6px}
.socials span{width:24px;height:24px;border-radius:50%;background:var(--blue)}
.socials span:nth-child(3){background:#d9453b}
.socials span:nth-child(4){background:#bbb}
.nav{height:50px;background:var(--blue)}
.nav .wrap{display:flex;height:50px;align-items:center}
.nav a{color:var(--white);text-decoration:none;font-size:14px;font-weight:600;margin-right:58px}
.nav a:first-child{margin-left:0}
.nav .book{margin-left:auto;margin-right:0;background:var(--green);height:50px;line-height:50px;padding:0 18px}
/* hero */
.hero{height:504px;position:relative;background:linear-gradient(180deg,#7fb6e6 0%,#b8d8ef 42%,#3f6e2a 62%,#5f9a33 80%,#77ad3f 100%)}
.hero-title{position:absolute;left:767px;top:340px;color:var(--white);font-weight:700;font-size:48px;line-height:1;letter-spacing:1px}
.hero-title small{display:block;font-size:40px;font-weight:600}
.hero-btn{position:absolute;left:764px;top:454px;background:var(--blue-dark);color:var(--white);font-size:14px;font-weight:700;padding:12px 22px}
.dots{position:absolute;left:572px;top:624px;display:flex;gap:6px}
.dots span{width:13px;height:13px;border-radius:50%;border:2px solid var(--white)}
.dots span:first-child{background:var(--white)}
/* welcome */
.welcome{height:396px;padding-top:64px}
.welcome .wrap{display:flex;gap:0}
.welcome-text{width:320px}
.welcome-text h2{font-size:29px;font-weight:400;line-height:1.1}
.welcome-text h2 b{display:block;font-size:38px;font-weight:400}
.welcome-text p{font-size:12px;color:var(--muted);line-height:1.7;margin-top:16px}
.feature{width:310px;margin-left:25px}
.feature:first-of-type{margin-left:40px}
.photo{display:block}
.feature .photo{height:200px}
.feature h3{font-size:19px;font-weight:400;margin-top:12px}
.feature p{font-size:12px;color:var(--muted);line-height:1.6;margin-top:8px}
/* services */
.services{height:550px;background:var(--light);padding-top:46px;text-align:center}
.section-title{font-size:31px;font-weight:400;letter-spacing:1px}
.section-lead{font-size:12px;color:var(--muted);line-height:1.7;width:740px;margin:16px auto 0}
.cards{display:flex;gap:28px;margin-top:56px}
.card{width:316px;height:305px;background:var(--white);box-shadow:0 2px 6px rgba(0,0,0,.15);padding:30px 22px 0}
.card h4{font-size:13px;font-weight:600;line-height:1.5;margin-top:26px;text-transform:uppercase}
.card p{font-size:12px;color:var(--muted);line-height:1.7;margin-top:12px}
.more{display:inline-block;margin-top:14px;border:1px solid var(--blue);color:var(--blue);font-size:11px;padding:4px 12px;border-radius:3px}
/* testimonial */
.testimonial{height:339px;background:linear-gradient(90deg,#b9b9b9,#a9a9a9 60%,#cfcfcf 80%,#a6a6a6);text-align:center;padding-top:64px;color:var(--white)}
.quote-mark{font-size:110px;line-height:.8;font-weight:700}
.testimonial p{font-size:13px;line-height:1.7;width:800px;margin:24px auto 0}
.testimonial cite{display:block;font-style:italic;font-size:18px;margin-top:22px}
.bars{display:flex;justify-content:center;gap:4px;margin-top:28px}
.bars span{width:30px;height:3px;background:rgba(255,255,255,.6)}
.bars span:first-child{background:var(--white)}
/* patients & doctors */
.people{height:504px;padding-top:52px}
.people .wrap{display:flex}
.col-head{font-size:26px;font-weight:600;letter-spacing:.5px}
.patients{width:474px}
.video{height:298px;margin-top:42px;position:relative;background:linear-gradient(135deg,#9cbf6a,#d9c4a3 50%,#8a9f5e)}
.video-bar{position:absolute;left:0;right:0;top:0;height:36px;background:rgba(0,0,0,.5);color:var(--white);font-size:12px;padding:10px 14px}
.play{position:absolute;left:215px;top:135px;width:50px;height:36px;background:rgba(0,0,0,.6);border-radius:6px}
.play::after{content:"";position:absolute;left:19px;top:10px;border-left:14px solid var(--white);border-top:8px solid transparent;border-bottom:8px solid transparent}
.doctors{margin-left:56px;width:478px}
.doctors .col-head{display:flex;justify-content:space-between}
.doctors .col-head span{color:var(--blue);font-size:24px}
.doctor{display:flex;margin-top:42px;gap:28px}
.doctor+.doctor{margin-top:30px}
.doctor .photo{width:212px;height:136px;background:linear-gradient(135deg,#e6eef3,#b8c9d6)}
.doctor h5{font-size:20px;color:var(--blue);font-weight:600;margin-top:-6px}
.doctor .role{font-size:13px;font-weight:600;margin-top:2px}
.doctor .contact{display:flex;gap:10px;align-items:center;font-size:12px;color:var(--muted);line-height:1.8;margin-top:10px}
.doctor .note{font-size:12px;color:var(--muted);margin-top:12px}
/* news */
.news{height:600px;background:var(--light);padding-top:46px;text-align:center}
.news .cards{gap:30px;margin-top:44px}
.news-card{width:316px;height:389px;background:var(--white);box-shadow:0 2px 6px rgba(0,0,0,.12);text-align:left}
.news-card .photo{height:198px}
.news-body{padding:22px 22px 0}
.date{display:inline-block;background:var(--blue);color:var(--white);font-size:11px;font-weight:600;padding:4px 10px}
.news-card h4{font-size:13px;font-weight:600;line-height:1.5;margin-top:14px}
.news-card p{font-size:12px;color:var(--muted);line-height:1.7;margin-top:10px}
/* footer */
.footer{height:309px;background:var(--blue);position:relative;color:var(--white);padding-top:70px}
.wave{position:absolute;left:0;top:-22px;width:1200px;height:40px}
.footer .wrap{display:flex}
.fcol h6{font-size:20px;font-weight:600;letter-spacing:.5px}
.fcol{font-size:12px;line-height:1.7}
.f-contact{width:318px}
.f-contact p{margin-top:18px}
.frow{display:flex;gap:14px;align-items:center;margin-top:14px}
.f-links{width:258px}
.f-links ul{list-style:none;margin-top:16px}
.f-links li{line-height:1.77;font-size:11px}
.f-links li::before{content:"\25B8";margin-right:8px}
.f-news{width:330px}
.f-news p{margin-top:14px}
.f-news .field{width:246px;height:42px;background:var(--white);color:#888;font-size:11px;padding:13px 12px;margin-top:16px}
.f-news .sub{display:inline-block;background:var(--green);font-weight:700;font-size:12px;padding:12px 16px;margin-top:16px}
.f-social ul{list-style:none;margin-top:16px}
.f-social li{display:flex;align-items:center;gap:10px;margin-bottom:11px;font-size:13px}
.f-social li span{width:24px;height:24px;border-radius:50%;border:1.5px solid var(--white)}
.bottom{height:57px;display:flex;align-items:center}
.bottom .wrap{display:flex;align-items:center}
.bottom small{font-size:12px;color:var(--ink)}
.partner{margin-left:auto;display:flex;align-items:center;gap:8px;font-size:26px;font-weight:600;color:#26466d}
.partner span{width:22px;height:22px;border-radius:50%;background:#26466d}
</style>
</head>
<body>

<header class="topbar">
  <div class="wrap">
    <div class="brand"><span class="brand-dot"></span><span class="brand-name">Bright Harbor</span></div>
    <div class="info">
      <svg width="36" height="36" viewBox="0 0 36 36"><circle cx="18" cy="18" r="16" fill="none" stroke="#2f8fef" stroke-width="2"/><path d="M12 11c1-1 3 0 3 1l1 3-2 2c1 2 3 4 5 5l2-2 3 1c1 0 2 2 1 3l-2 2c-6 0-13-7-13-13z" fill="#2f8fef"/></svg>
      <div>info@brightharbormed.com<br><strong>Phone : 603-555-0142</strong></div>
    </div>
    <div class="info hours">
      <svg width="36" height="36" viewBox="0 0 36 36"><circle cx="18" cy="19" r="14" fill="none" stroke="#2f8fef" stroke-width="2"/><path d="M18 11v8l5 4" stroke="#2f8fef" stroke-width="2" fill="none"/></svg>
      <div>Monday – Friday<br>08:00 – 20:00</div>
    </div>
    <div class="socials"><span></span><span></span><span></span><span></span></div>
  </div>
</header>

<nav class="nav">
  <div class="wrap">
    <a href="#">HOME</a><a href="#">ABOUT US</a><a href="#">OUR SERVICES</a><a href="#">PATIENT INFO</a><a href="#">BLOG</a><a href="#">CONTACT US</a>
    <a href="#" class="book">BOOK APPOINTMENT</a>
  </div>
</nav>

<section class="hero" role="img" aria-label="Older couple jogging across a sunny park lawn">
  <div class="hero-title">ADVANCED<small>CARE PLANNING</small></div>
  <div class="hero-btn">MAKE AN APPOINTMENT</div>
  <div class="dots"><span></span><span></span><span></span></div>
</section>

<section class="welcome">
  <div class="wrap">
    <div class="welcome-text">
      <h2>Welcome To<b>BRIGHT HARBOR</b></h2>
      <p>Advanced Directives are legally binding documents that spell out what type of medical care you would - or would not - want done to you. We often assume that our families or medical professionals will make "the right decision", but this can be an anguishing process - and often does not accurately reflects the patient's true desires. By making your choices clear, your family and caregivers can honor your wishes when you cannot speak for yourself.</p>
    </div>
    <article class="feature">
      <div class="photo" role="img" aria-label="Close-up of hands holding a patient's hand" style="background:linear-gradient(135deg,#3b8fc9,#e3b9a3 50%,#c99680)"></div>
      <h3>Advanced Care Planning</h3>
      <p>Lorem ipsum dolor sit amet, consectetur adipiscing elit, sed do eiusmod tempor incididunt ut labore</p>
    </article>
    <article class="feature">
      <div class="photo" role="img" aria-label="Caregiver helping a smiling older woman walk" style="background:linear-gradient(135deg,#c9c3b6,#e6d9cc 50%,#8f9aa3)"></div>
      <h3>Advanced Care Planning</h3>
      <p>Lorem ipsum dolor sit amet, consectetur adipiscing elit, sed do eiusmod tempor incididunt ut labore</p>
    </article>
  </div>
</section>

<section class="services">
  <div class="wrap">
    <h2 class="section-title">OUR SERVICES</h2>
    <p class="section-lead">Advanced Directives are legally binding documents that spell out what type of medical care you would - or would not - want done to you. We often assume that our families or medical professionals will make "the right decision", but this can be an anguishing process</p>
    <div class="cards">
      <div class="card">
        <svg width="80" height="80" viewBox="0 0 80 80"><g stroke="#2f8fef" stroke-width="4" stroke-linecap="round"><path d="M40 6v10M40 64v10M6 40h10M64 40h10M16 16l7 7M57 57l7 7M64 16l-7 7M23 57l-7 7"/></g><circle cx="40" cy="34" r="6" fill="#2f8fef"/><path d="M28 54l12-12 12 12" fill="none" stroke="#2f8fef" stroke-width="4"/></svg>
        <h4>Individualized Physician-Guided Healthcare Planning</h4>
        <p>Advanced Directives are legally binding documents that spell out what type of medical care you would - or would not - want done to you.</p>
        <span class="more">READ MORE ●</span>
      </div>
      <div class="card">
        <svg width="80" height="80" viewBox="0 0 80 80"><path d="M40 70L12 42C2 32 8 12 24 12c8 0 13 5 16 10 3-5 8-10 16-10 16 0 22 20 12 30z" fill="none" stroke="#2f8fef" stroke-width="4"/><path d="M26 42l10-8 10 8 8-6" fill="none" stroke="#2f8fef" stroke-width="4"/></svg>
        <h4>Helping Navigate Complex Medical Situations</h4>
        <p>Advanced Directives are legally binding documents that spell out what type of medical care you would - or would not - want done to you.</p>
        <span class="more">READ MORE ●</span>
      </div>
      <div class="card">
        <svg width="80" height="80" viewBox="0 0 80 80"><path d="M40 44L28 32c-5-5-2-14 5-14 3 0 5 2 7 4 2-2 4-4 7-4 7 0 10 9 5 14z" fill="#2f8fef"/><path d="M8 42l16 22h32l16-22-6-3-14 14H28L14 39z" fill="#2f8fef"/></svg>
        <h4>Creating Legally Binding Advanced Directives</h4>
        <p>Advanced Directives are legally binding documents that spell out what type of medical care you would - or would not - want done to you.</p>
        <span class="more">READ MORE ●</span>
      </div>
    </div>
  </div>
</section>

<section class="testimonial" role="img" aria-label="Faded portrait of a smiling older woman behind the quote">
  <div class="quote-mark">”</div>
  <p>Lorem ipsum dolor sit amet, consectetur adipiscing elit, sed do eiusmod tempor incididunt ut labore et dolore magna aliqua. Ut enim ad minim veniam, quis nostrud exercitation ullamco laboris nisi ut aliquip ex ea commodo consequat. Duis aute irure dolor in reprehenderit in voluptate velit esse cillum dolore eu fugiat nulla Sed ut perspiciatis unde omnis iste natus error sit voluptatem accusantium</p>
  <cite>- Helen, mother of Sam, 3 years old</cite>
  <div class="bars"><span></span><span></span><span></span></div>
</section>

<section class="people">
  <div class="wrap">
    <div class="patients">
      <h2 class="col-head">WHAT OUR PATIENTS SAY</h2>
      <div class="video" role="img" aria-label="Video still of a smiling older couple outdoors">
        <div class="video-bar">Advanced Care Planning</div>
        <div class="play"></div>
      </div>
    </div>
    <div class="doctors">
      <h2 class="col-head">MEET THE DOCTORS <span>‹ ›</span></h2>
      <div class="doctor">
        <div class="photo" role="img" aria-label="Doctor examining a young patient"></div>
        <div>
          <h5>ALEX MORENO</h5>
          <div class="role">ADVANCED CARE PLANNING</div>
          <div class="contact"><svg width="22" height="22" viewBox="0 0 22 22"><path d="M5 3c1-1 3 0 3 1l1 3-2 2c1 2 3 4 5 5l2-2 3 1c1 0 2 2 1 3l-2 2C10 18 4 12 4 5z" fill="#bbb"/></svg><div>alex@brightharbormed.com<br>Phone : (906) - 555 - 0188</div></div>
          <div class="note">Sed ut perspiciatis unde omnis iste natus</div>
        </div>
      </div>
      <div class="doctor">
        <div class="photo" role="img" aria-label="Doctor consulting with an older patient"></div>
        <div>
          <h5>ALEX MORENO</h5>
          <div class="role">ADVANCED CARE PLANNING</div>
          <div class="contact"><svg width="22" height="22" viewBox="0 0 22 22"><path d="M5 3c1-1 3 0 3 1l1 3-2 2c1 2 3 4 5 5l2-2 3 1c1 0 2 2 1 3l-2 2C10 18 4 12 4 5z" fill="#bbb"/></svg><div>alex@brightharbormed.com<br>Phone : (906) - 555 - 0188</div></div>
          <div class="note">Sed ut perspiciatis unde omnis iste natus</div>
        </div>
      </div>
    </div>
  </div>
</section>

<section class="news">
  <div class="wrap">
    <h2 class="section-title">LATEST NEWS</h2>
    <p class="section-lead">Lorem ipsum dolor sit amet, consectetuer. Proin gravida nibh vel velit auctor aliquetenean. Cum sociis Theme natoque penatibus et magnis dis parturient nascetur ridiculus mus</p>
    <div class="cards">
      <article class="news-card">
        <div class="photo" role="img" aria-label="Smiling older woman in a blue shirt" style="background:linear-gradient(135deg,#9fc3df,#e8dccb 55%,#7ea3c6)"></div>
        <div class="news-body"><span class="date">May 20, 2016</span><h4>INDIVIDUALIZED PHYSICIAN-GUIDED HEALTHCARE PLANNING</h4><p>Advanced Directives are legally binding documents that spell out what type of medical care you would or would not - want done to you.</p></div>
      </article>
      <article class="news-card">
        <div class="photo" role="img" aria-label="Older couple embracing in a sunny garden" style="background:linear-gradient(135deg,#8cb04f,#e7d2b4 50%,#6d8f3a)"></div>
        <div class="news-body"><span class="date">May 20, 2016</span><h4>INDIVIDUALIZED PHYSICIAN-GUIDED HEALTHCARE PLANNING</h4><p>Advanced Directives are legally binding documents that spell out what type of medical care you would or would not - want done to you.</p></div>
      </article>
      <article class="news-card">
        <div class="photo" role="img" aria-label="Person doing a yoga pose on a rock by a lake" style="background:linear-gradient(180deg,#bcd0d6,#8fb0b4 50%,#6d7f78)"></div>
        <div class="news-body"><span class="date">May 20, 2016</span><h4>INDIVIDUALIZED PHYSICIAN-GUIDED HEALTHCARE PLANNING</h4><p>Advanced Directives are legally binding documents that spell out what type of medical care you would or would not - want done to you.</p></div>
      </article>
    </div>
  </div>
</section>

<footer class="footer">
  <svg class="wave" viewBox="0 0 1200 40" preserveAspectRatio="none"><path d="M0 40C300 0 800 0 1200 30V40z" fill="#2f8fef"/><path d="M0 38C300 -2 800 -2 1200 28" fill="none" stroke="#38c21f" stroke-width="6"/></svg>
  <div class="wrap">
    <div class="fcol f-contact">
      <h6>CONTACT US</h6>
      <p>Dana Whitfield, MD Harbor Road,<br>Ste 200 Concord, NH</p>
      <div class="frow"><svg width="18" height="18" viewBox="0 0 22 22"><path d="M5 3c1-1 3 0 3 1l1 3-2 2c1 2 3 4 5 5l2-2 3 1c1 0 2 2 1 3l-2 2C10 18 4 12 4 5z" fill="#fff"/></svg><div>Call Us : 603-555-0142<br>603-555-0147</div></div>
      <div class="frow"><svg width="20" height="16" viewBox="0 0 20 16"><rect x="1" y="1" width="18" height="14" fill="none" stroke="#fff" stroke-width="1.5"/><path d="M1 1l9 8 9-8" fill="none" stroke="#fff" stroke-width="1.5"/></svg><div>info@brightharbormed.com</div></div>
    </div>
    <div class="fcol f-links">
      <h6>QUICK LINKS</h6>
      <ul><li>HOME</li><li>ABOUT US</li><li>ADVANCED CARE PLANNING</li><li>TESTIMONIALS</li><li>BLOG</li><li>CONTACT US</li></ul>
    </div>
    <div class="fcol f-news">
      <h6>SIGN UP FOR NEWSLETTER</h6>
      <p>Excepteur sint occaecat cupidatat non proident, sunt in culpa qui officia deserunt</p>
      <div class="field">Enter email</div>
      <span class="sub">SUBSCRIPTION</span>
    </div>
    <div class="fcol f-social">
      <h6>SOCIAL</h6>
      <ul><li><span></span>Community</li><li><span></span>Updates</li><li><span></span>Network</li><li><span></span>Videos</li></ul>
    </div>
  </div>
</footer>

<div class="bottom">
  <div class="wrap">
    <small>2016 © Copyrights Bright Harbor.All Rights Reserved</small>
    <div class="partner"><span></span>lumenfold</div>
  </div>
</div>

</body>
</html>
```